Business Card Design Project

Business card based on attached logo

Todd Merrick
Todd@lorvantest.com
877-514-9073 ext. 318
Www.LorvanTest.com

Industry/Entity Type

Business

```html
<!DOCTYPE html>
<html lang="en">
<head>
<meta charset="utf-8">
<title>LorvanTest Business Cards</title>
<link rel="stylesheet" href="https://fonts.googleapis.com/css2?family=Archivo+Black&family=Arimo:wght@400;700&display=swap">
<style>
  :root {
    --board-light: #d9d9d9;
    --board-dark: #9a9a9a;
    --brand-red: #e5232b;
    --brand-red-deep: #c3202a;
    --accent-red: #ee3a3f;
    --ink: #231f20;
    --paper: #ffffff;
    --charcoal: #1e1e1e;
    --charcoal-soft: #3a3a3a;
  }
  * { margin: 0; padding: 0; box-sizing: border-box; }
  html, body { width: 1200px; height: 729px; overflow: hidden; }
  body {
    position: relative;
    background: radial-gradient(ellipse at 50% 45%, var(--board-light) 0%, #bdbdbd 55%, var(--board-dark) 100%);
    font-family: "Arimo", Arial, sans-serif;
  }
  .card {
    position: absolute;
    width: 536px;
    height: 305px;
    overflow: hidden;
  }
  .card--white { left: 41px; top: 45px; background: var(--paper); border: 1px solid #8a8a8a; }
  .card--red { left: 612px; top: 45px; background: linear-gradient(135deg, var(--brand-red) 0%, var(--brand-red-deep) 100%); }
  .card--light { left: 41px; top: 381px; background: linear-gradient(90deg, #d2d2d2 0%, #f2f2f2 50%, #d2d2d2 100%); border: 1px solid #b5b5b5; }
  .card--dark { left: 612px; top: 381px; background: radial-gradient(ellipse at 55% 45%, var(--charcoal-soft) 0%, var(--charcoal) 75%); }

  .brand {
    position: absolute;
    display: flex;
    align-items: center;
    gap: 14px;
    font-family: "Archivo Black", "Arial Black", sans-serif;
    font-size: 52px;
    line-height: 1;
    letter-spacing: -1px;
  }
  .brand__square { width: 30px; height: 30px; flex: none; }
  .card--white .brand { left: 0; right: 0; top: 62px; justify-content: center; color: var(--ink); }
  .card--white .brand__square { background: var(--accent-red); }
  .card--red .brand { left: 32px; top: 44px; color: var(--paper); font-size: 58px; }
  .card--dark .brand { left: 0; right: 0; top: 62px; justify-content: center; color: var(--paper); }
  .card--dark .brand__square { background: var(--paper); }

  .tagline, .url, .person, .contact {
    position: absolute;
    white-space: nowrap;
    line-height: 1.2;
  }
  .tagline { font-size: 16px; letter-spacing: 0.6px; }
  .person { font-size: 17px; font-weight: 700; letter-spacing: 0.4px; }
  .contact { font-size: 13px; letter-spacing: 0.3px; }
  .url { font-size: 15px; letter-spacing: 2.4px; }
  .centered { left: 0; right: 0; text-align: center; }

  .card--white .tagline { top: 140px; color: var(--brand-red); }
  .card--white .person { top: 184px; color: var(--ink); }
  .card--white .contact { top: 210px; color: var(--ink); }
  .card--white .url { top: 262px; color: var(--ink); }

  .card--red .tagline { left: 34px; top: 124px; color: var(--paper); }
  .card--red .person { left: 34px; top: 176px; color: var(--paper); }
  .card--red .contact { left: 34px; top: 202px; color: var(--paper); }
  .card--red .url { left: 34px; top: 266px; color: var(--paper); }
  .card--red .panel-mark {
    position: absolute;
    right: 0; top: 150px;
    width: 96px; height: 155px;
    background: rgba(255,255,255,0.12);
  }

  .card--light .block-mark {
    position: absolute;
    left: 50%; top: 30px;
    width: 104px; height: 104px;
    margin-left: -52px;
    background: var(--accent-red);
  }
  .card--light .tagline { top: 150px; color: var(--ink); }
  .card--light .person { top: 188px; color: var(--ink); }
  .card--light .contact { top: 214px; color: var(--ink); }
  .card--light .url { top: 262px; color: var(--ink); }

  .card--dark .tagline { top: 140px; color: var(--paper); }
  .card--dark .person { top: 184px; color: var(--paper); }
  .card--dark .contact { top: 210px; color: var(--paper); }
  .card--dark .url { top: 262px; color: var(--paper); }
</style>
</head>
<body>
  <section class="card card--white">
    <div class="brand"><span>LorvanTest</span><span class="brand__square"></span></div>
    <p class="tagline centered">Expert Online HIPAA Training</p>
    <p class="person centered">Todd Merrick</p>
    <p class="contact centered">Todd@lorvantest.com &nbsp;|&nbsp; 877-514-9073 ext. 318</p>
    <p class="url centered">www.lorvantest.com</p>
  </section>

  <section class="card card--red">
    <div class="panel-mark"></div>
    <div class="brand"><span>LorvanTest</span></div>
    <p class="tagline">Expert Online HIPAA Training</p>
    <p class="person">Todd Merrick</p>
    <p class="contact">Todd@lorvantest.com &nbsp;|&nbsp; 877-514-9073 ext. 318</p>
    <p class="url">www.lorvantest.com</p>
  </section>

  <section class="card card--light">
    <div class="block-mark"></div>
    <p class="tagline centered">Expert Online HIPAA Training</p>
    <p class="person centered">Todd Merrick</p>
    <p class="contact centered">Todd@lorvantest.com &nbsp;|&nbsp; 877-514-9073 ext. 318</p>
    <p class="url centered">www.lorvantest.com</p>
  </section>

  <section class="card card--dark">
    <div class="brand"><span>LorvanTest</span><span class="brand__square"></span></div>
    <p class="tagline centered">Expert Online HIPAA Training</p>
    <p class="person centered">Todd Merrick</p>
    <p class="contact centered">Todd@lorvantest.com &nbsp;|&nbsp; 877-514-9073 ext. 318</p>
    <p class="url centered">www.lorvantest.com</p>
  </section>
</body>
</html>
```